Business card design Needed for new logo / Construction business, home extensions and new builds

We need a business card design using our new logo files which i will attach to this project :)

We are a small construction business specialising in home extensions, new builds and property development. We are very ambitious and would appreciate professional and elegant designs for our new business card.

Very serious about using the services on MakerQuarry and recently acquired our new logo from here :)

Please get involved, i will feedback when i can as i am very busy but can respond daily, thanks

Target Market(s)

People that want to build onto their houses, new building developments or adding too their existing property

Industry/Entity Type

Construction

Contact Information for Business Card

Renwick Tolliver Construction, Lionel Ashby (Managing Director), Tel 07822254961, email - info@renwick-tolliver, www.renwick-tolliver.co.uk

Colors

Designer to choose colors to be used in the design.

Requirements
Must have
• I like a deep grey on the back please. A lot of you have provided black from and back, try mixing things up a little. The black looks cool 😎 Thanks

```html
<!DOCTYPE html>
<html lang="en">
<head>
<meta charset="utf-8">
<title>Renwick Tolliver Construction – Business Card</title>
<link rel="stylesheet" href="https://fonts.googleapis.com/css2?family=Open+Sans:wght@400;600;700&display=swap">
<style>
  :root {
    --backdrop: #232323;
    --card-grey: #6f7273;
    --card-grey-light: #7b7e7f;
    --card-dark: #1f1f22;
    --gold: #e2a72a;
    --gold-deep: #c98d16;
    --silver: #d4d6d8;
    --silver-deep: #8e9194;
    --ink-light: #f2f2f2;
    --emboss: #55585a;
    --rule: #bfc2c4;
  }
  * { margin: 0; padding: 0; box-sizing: border-box; }
  html, body {
    width: 1200px; height: 780px; overflow: hidden;
    background: var(--backdrop);
    font-family: "Open Sans", Arial, sans-serif;
  }
  .canvas { position: relative; width: 1200px; height: 780px; }

  .card {
    position: absolute;
    width: 560px; height: 320px;
    border-radius: 22px;
    border: 3px solid var(--gold);
    box-shadow: 0 18px 40px rgba(0,0,0,.55);
    overflow: hidden;
  }

  /* Front: deep grey with company name */
  .card--front {
    left: 50px; top: 60px;
    background: radial-gradient(ellipse at 50% 45%, var(--card-grey-light), var(--card-grey) 70%);
    display: flex; flex-direction: column; align-items: center; justify-content: center;
    gap: 14px;
  }
  .brand-mark {
    width: 46px; height: 46px;
    background: var(--emboss);
    border-radius: 4px;
  }
  .brand-name {
    color: var(--emboss);
    font-weight: 700;
    text-align: center;
    text-transform: uppercase;
    letter-spacing: .08em;
    line-height: 1.25;
  }
  .brand-name__primary { display: block; font-size: 34px; }
  .brand-name__secondary { display: block; font-size: 20px; letter-spacing: .22em; }

  /* Back: black with contact details */
  .card--back {
    left: 590px; top: 400px;
    background: linear-gradient(135deg, #27272b, var(--card-dark) 60%);
    color: var(--ink-light);
  }
  .person {
    position: absolute; left: 46px; top: 118px;
  }
  .person__name { font-size: 38px; font-weight: 700; line-height: 1.05; }
  .person__first {
    background: linear-gradient(180deg, var(--silver), var(--silver-deep));
    -webkit-background-clip: text; background-clip: text; color: transparent;
  }
  .person__last {
    background: linear-gradient(180deg, #f3bd3c, var(--gold-deep));
    -webkit-background-clip: text; background-clip: text; color: transparent;
  }
  .person__role { font-size: 16px; font-weight: 600; margin-top: 4px; margin-left: 112px; }

  .divider {
    position: absolute; left: 318px; top: 86px;
    width: 1px; height: 120px;
    background: linear-gradient(180deg, transparent, var(--rule) 30%, var(--rule) 70%, transparent);
  }
  .contacts {
    position: absolute; left: 334px; top: 96px;
    list-style: none;
    font-size: 14px; line-height: 1;
  }
  .contacts__item { display: flex; align-items: center; gap: 8px; margin-bottom: 14px; }
  .contacts__icon { width: 14px; height: 14px; flex: none; }

  .address {
    position: absolute; left: 46px; right: 40px; bottom: 40px;
    font-size: 15px; text-align: right; letter-spacing: .01em;
  }
</style>
</head>
<body>
<main class="canvas">

  <section class="card card--front" aria-label="Card front">
    <span class="brand-mark" aria-hidden="true"></span>
    <h1 class="brand-name">
      <span class="brand-name__primary">Renwick Tolliver</span>
      <span class="brand-name__secondary">Construction</span>
    </h1>
  </section>

  <section class="card card--back" aria-label="Card back">
    <div class="person">
      <p class="person__name"><span class="person__first">Lionel</span> <span class="person__last">Ashby</span></p>
      <p class="person__role">Managing Director</p>
    </div>

    <span class="divider" aria-hidden="true"></span>

    <ul class="contacts">
      <li class="contacts__item">
        <svg class="contacts__icon" viewBox="0 0 24 24" aria-hidden="true">
          <path fill="#e2a72a" d="M6.6 10.8a15.1 15.1 0 0 0 6.6 6.6l2.2-2.2c.3-.3.7-.4 1-.2 1.1.4 2.3.6 3.6.6.6 0 1 .4 1 1V20c0 .6-.4 1-1 1A17 17 0 0 1 3 4c0-.6.4-1 1-1h3.5c.6 0 1 .4 1 1 0 1.3.2 2.5.6 3.6.1.3 0 .7-.2 1z"/>
        </svg>
        <span>0782 225 4961</span>
      </li>
      <li class="contacts__item">
        <svg class="contacts__icon" viewBox="0 0 24 24" aria-hidden="true">
          <rect x="2" y="5" width="20" height="14" rx="2" fill="#e2a72a"/>
          <path d="M3 6.5l9 6.5 9-6.5" fill="none" stroke="#1f1f22" stroke-width="1.8"/>
        </svg>
        <span>info@renwick-tolliver.co.uk</span>
      </li>
      <li class="contacts__item">
        <svg class="contacts__icon" viewBox="0 0 24 24" aria-hidden="true">
          <circle cx="12" cy="12" r="10" fill="#e2a72a"/>
          <path d="M2 12h20M12 2c3 3 3 17 0 20M12 2c-3 3-3 17 0 20" fill="none" stroke="#1f1f22" stroke-width="1.5"/>
        </svg>
        <span>www.renwick-tolliver.co.uk</span>
      </li>
    </ul>

    <p class="address">Harrow Lane, Eastbrook Wellmouth, WM4 2JT</p>
  </section>

</main>
</body>
</html>
```